Frostvale Harborline LLC

we need a business card design

Industry/Entity Type

hvac

Contact Information for Business Card

my logo

Requirements
Must have
• my logo and same colors

```html
<!DOCTYPE html>
<html lang="en">
<head>
<meta charset="utf-8">
<title>Frostvale Harborline LLC – Business Card</title>
<link rel="stylesheet" href="https://fonts.googleapis.com/css2?family=Montserrat:wght@400;500;700&display=swap">
<style>
  :root {
    --brand-blue: #0a5ea8;
    --deep-blue: #0b5aa6;
    --sky-blue: #0bb0e0;
    --sun-orange: #f5b84c;
    --ink: #1c1c1c;
    --paper: #ffffff;
    --backdrop: #e4e4e6;
  }
  * { box-sizing: border-box; margin: 0; padding: 0; }
  html, body {
    width: 1200px;
    height: 1108px;
    overflow: hidden;
    background: var(--backdrop);
    font-family: "Montserrat", sans-serif;
  }
  .canvas { position: relative; width: 1200px; height: 1108px; }

  .card { position: absolute; overflow: hidden; }

  /* Front side */
  .card--front {
    left: 219px; top: 50px; width: 776px; height: 473px;
    background: var(--paper);
  }
  .brand-lockup {
    position: absolute;
    left: 131px; top: 205px; width: 245px;
    display: flex; align-items: center; gap: 10px;
  }
  .brand-lockup__dot {
    flex: none; width: 18px; height: 18px; border-radius: 50%;
    background: var(--sun-orange);
  }
  .brand-lockup__name {
    font-weight: 700; font-size: 25px; line-height: 1.15;
    color: var(--deep-blue);
  }
  .contact-block {
    position: absolute;
    left: 392px; top: 162px; height: 206px;
    border-left: 2px solid var(--deep-blue);
    padding-left: 14px;
  }
  .contact-block__name {
    font-weight: 700; font-size: 29px; line-height: 1; color: var(--deep-blue);
  }
  .contact-block__role {
    font-size: 17px; color: var(--ink); margin-top: 8px;
  }
  .contact-block__address {
    font-size: 17px; line-height: 22px; color: var(--ink); margin-top: 14px;
  }
  .contact-list { list-style: none; margin-top: 10px; }
  .contact-list__item {
    display: flex; align-items: center; gap: 10px;
    font-size: 17px; line-height: 28px; color: var(--ink);
  }
  .contact-list__icon { width: 18px; height: 18px; flex: none; }
  .stripe-bar { position: absolute; left: 0; bottom: 0; width: 776px; height: 28px; }

  /* Back side */
  .card--back {
    left: 217px; top: 568px; width: 778px; height: 457px;
    background: var(--brand-blue);
    display: flex; align-items: center; justify-content: center; gap: 18px;
  }
  .back-lockup__dot {
    width: 34px; height: 34px; border-radius: 50%; background: var(--sun-orange);
  }
  .back-lockup__name {
    font-weight: 700; font-size: 50px; line-height: 1.1; color: var(--paper);
  }
</style>
</head>
<body>
<main class="canvas">

  <section class="card card--front" aria-label="Business card front">
    <div class="brand-lockup">
      <span class="brand-lockup__dot"></span>
      <span class="brand-lockup__name">Frostvale<br>Harborline LLC</span>
    </div>

    <div class="contact-block">
      <h1 class="contact-block__name">Adrian Kessler</h1>
      <p class="contact-block__role">Managing Director</p>
      <p class="contact-block__address">48 Birchwood Lane,<br>Marlow, NY 14207</p>
      <ul class="contact-list">
        <li class="contact-list__item">
          <svg class="contact-list__icon" viewBox="0 0 18 18" aria-hidden="true">
            <rect x="4" y="1" width="10" height="16" rx="2" fill="none" stroke="#f5b84c" stroke-width="2"/>
            <rect x="7.5" y="13.5" width="3" height="1.5" fill="#f5b84c"/>
          </svg>
          +1 (555) 214-7830
        </li>
        <li class="contact-list__item">
          <svg class="contact-list__icon" viewBox="0 0 18 18" aria-hidden="true">
            <rect x="2" y="5" width="14" height="9" fill="#f5b84c"/>
            <path d="M2 5 L9 10 L16 5" fill="none" stroke="#ffffff" stroke-width="1.3"/>
          </svg>
          hello@frostvalellc.com
        </li>
        <li class="contact-list__item">
          <svg class="contact-list__icon" viewBox="0 0 18 18" aria-hidden="true">
            <circle cx="9" cy="9" r="7.5" fill="#f5b84c"/>
            <path d="M1.5 9 H16.5 M9 1.5 C5.5 5 5.5 13 9 16.5 M9 1.5 C12.5 5 12.5 13 9 16.5" fill="none" stroke="#ffffff" stroke-width="1"/>
          </svg>
          www.frostvalellc.com
        </li>
      </ul>
    </div>

    <svg class="stripe-bar" viewBox="0 0 776 28" preserveAspectRatio="none" aria-hidden="true">
      <polygon points="0,0 252,0 226,28 0,28" fill="#0b5aa6"/>
      <polygon points="262,0 513,0 487,28 236,28" fill="#0bb0e0"/>
      <polygon points="523,0 776,0 776,28 497,28" fill="#f5b84c"/>
    </svg>
  </section>

  <section class="card card--back" aria-label="Business card back">
    <span class="back-lockup__dot"></span>
    <span class="back-lockup__name">Frostvale<br>Harborline LLC</span>
  </section>

</main>
</body>
</html>
```